Need to create logo for Harbourline Ventures Ltd

We supply the above mention products all around NZ. Trading under the company name Harbourline Ventures Ltd.

Industry/Entity Type

It Company

Contact Information for Business Card

Harbourline Ventures Ltd. 0800519203 0217043952 Brent@Talvora.co.nz contact Brent HOLM
Suppliers of Talvora Louvres, Aluminim Sable shutters, Fennroll curtains,Glow forge outdoor heaters,Caltex outdoor heaters

```html
<!DOCTYPE html>
<html lang="en">
<head>
<meta charset="utf-8">
<title>Harbourline Ventures Ltd — Business Card</title>
<link rel="stylesheet" href="https://fonts.googleapis.com/css2?family=Jost:wght@400&family=Open+Sans:wght@400;700&display=swap">
<style>
  :root {
    --backdrop: #e9e7e4;
    --card-white: #ffffff;
    --card-brown: #5b2620;
    --brand-red: #c9202c;
    --brand-charcoal: #403a37;
    --text-dark: #2b2b2b;
    --text-light: #f6f1ee;
  }
  * { margin: 0; padding: 0; box-sizing: border-box; }
  html, body {
    width: 1200px;
    height: 900px;
    overflow: hidden;
    background: var(--backdrop);
  }
  .stage {
    position: relative;
    width: 1200px;
    height: 900px;
  }
  .card {
    position: absolute;
    left: 290px;
    width: 620px;
    height: 354px;
    box-shadow: 0 6px 18px rgba(0, 0, 0, 0.18);
    overflow: hidden;
  }
  .card--back {
    top: 62px;
    background: var(--card-brown);
    display: flex;
    align-items: center;
    justify-content: center;
  }
  .back-name {
    font-family: "Jost", sans-serif;
    font-weight: 400;
    font-size: 34px;
    letter-spacing: 1px;
    color: var(--text-light);
    text-transform: uppercase;
  }
  .card--front {
    top: 484px;
    background: var(--card-white);
  }
  .front-shapes {
    position: absolute;
    inset: 0;
  }
  .holder-name {
    position: absolute;
    left: 92px;
    top: 30px;
    font-family: "Open Sans", sans-serif;
    font-weight: 700;
    font-size: 21px;
    color: var(--brand-red);
  }
  .contact-list {
    position: absolute;
    left: 36px;
    top: 168px;
    list-style: none;
    font-family: "Open Sans", sans-serif;
    font-size: 15px;
    line-height: 21px;
    color: var(--text-dark);
  }
  .contact-list li {
    display: flex;
    align-items: center;
    gap: 12px;
  }
  .contact-icon {
    width: 11px;
    height: 11px;
    flex: none;
  }
  .brand-mark {
    position: absolute;
    left: 330px;
    top: 112px;
    width: 260px;
    display: flex;
    flex-direction: column;
    align-items: center;
    gap: 14px;
  }
  .brand-dot {
    width: 46px;
    height: 46px;
    border-radius: 50%;
    background: var(--brand-charcoal);
  }
  .brand-name {
    font-family: "Jost", sans-serif;
    font-weight: 400;
    font-size: 19px;
    letter-spacing: 0.5px;
    color: var(--brand-charcoal);
    text-transform: uppercase;
    white-space: nowrap;
  }
</style>
</head>
<body>
<main class="stage">

  <section class="card card--back" aria-label="Business card, back">
    <p class="back-name">Harbourline Ventures Ltd</p>
  </section>

  <section class="card card--front" aria-label="Business card, front">
    <svg class="front-shapes" viewBox="0 0 620 354" width="620" height="354" aria-hidden="true">
      <polygon points="0,0 40,0 20,26 0,26" fill="var(--brand-red)"/>
      <polygon points="46,26 68,0 82,0 82,26" fill="var(--brand-charcoal)"/>
      <polygon points="0,262 302,262 290,282 0,282" fill="var(--brand-red)"/>
      <polygon points="306,294 620,294 620,330 284,330" fill="var(--brand-charcoal)"/>
    </svg>

    <h1 class="holder-name">Brent HOLM</h1>

    <ul class="contact-list">
      <li>
        <svg class="contact-icon" viewBox="0 0 11 11" aria-hidden="true">
          <rect x="2.5" y="0.5" width="6" height="10" rx="1" fill="none" stroke="var(--brand-red)" stroke-width="1.2"/>
        </svg>
        0800519203
      </li>
      <li>
        <svg class="contact-icon" viewBox="0 0 11 11" aria-hidden="true">
          <rect x="0.5" y="2" width="10" height="8.5" rx="1" fill="var(--brand-red)"/>
          <rect x="3" y="0.5" width="5" height="2.5" fill="var(--brand-red)"/>
        </svg>
        0217043952
      </li>
      <li>
        <svg class="contact-icon" viewBox="0 0 11 11" aria-hidden="true">
          <rect x="0.5" y="2" width="10" height="7" fill="var(--brand-red)"/>
          <polyline points="0.5,2 5.5,6 10.5,2" fill="none" stroke="#fff" stroke-width="1"/>
        </svg>
        Brent@Talvora.co.nz
      </li>
    </ul>

    <div class="brand-mark">
      <span class="brand-dot" aria-hidden="true"></span>
      <p class="brand-name">Harbourline Ventures Ltd</p>
    </div>
  </section>

</main>
</body>
</html>
```